Letterhead Design Project

I need letterhead designed for my law firm. It would also be used for web based stuff as well.

Industry/Entity Type

Law Firm

```html
<!DOCTYPE html>
<html lang="en">
<head>
<meta charset="utf-8">
<title>Harlow &amp; Penn — Letterhead</title>
<link rel="stylesheet" href="https://fonts.googleapis.com/css2?family=Source+Sans+3:wght@400;600&display=swap">
<style>
  :root {
    --paper: #ffffff;
    --ink-grey: #6d6e71;
    --navy: #2b2a66;
    --white: #ffffff;
  }
  * { margin: 0; padding: 0; box-sizing: border-box; }
  html, body { width: 844px; height: 1200px; overflow: hidden; background: var(--paper); }
  body { font-family: "Source Sans 3", Arial, sans-serif; color: var(--ink-grey); }

  .letterhead { position: relative; width: 844px; height: 1200px; background: var(--paper); }

  .sender { position: absolute; left: 68px; top: 32px; font-size: 17px; line-height: 20px; }
  .sender__address { margin-top: 13px; }

  .brand-name {
    position: absolute; left: 320px; top: 48px; width: 200px;
    text-align: center;
    font-size: 21px; font-weight: 600; letter-spacing: 0.5px;
    color: var(--navy);
  }

  .contact { position: absolute; left: 566px; top: 0; list-style: none; font-size: 17px; }
  .contact__item { position: absolute; left: 0; display: flex; align-items: center; height: 22px; white-space: nowrap; }
  .contact__item--phone { top: 49px; }
  .contact__item--email { top: 79px; }
  .contact__item--web { top: 104px; }
  .contact__icon {
    width: 18px; height: 18px; border-radius: 50%;
    background: var(--navy); color: var(--white);
    font-size: 11px; font-weight: 600; line-height: 18px; text-align: center;
    margin-right: 12px;
  }

  .footer-band { position: absolute; left: 0; bottom: 0; width: 844px; height: 15px; background: var(--navy); }
</style>
</head>
<body>
<main class="letterhead">
  <div class="sender">
    <p class="sender__name">Name</p>
    <p class="sender__role">Designation</p>
    <p class="sender__address">Address 01, ABC Street<br>XYZ lane, London , UK</p>
  </div>

  <p class="brand-name">HARLOW &amp; PENN</p>

  <ul class="contact">
    <li class="contact__item contact__item--phone"><span class="contact__icon">P</span>022 XXXXXXXXX</li>
    <li class="contact__item contact__item--email"><span class="contact__icon">E</span>name@websitename.com</li>
    <li class="contact__item contact__item--web"><span class="contact__icon">W</span>www.webname.com</li>
  </ul>

  <div class="footer-band"></div>
</main>
</body>
</html>
```